Local Flower Farm Needs Business Card Design

I need business cards designed for a flower farm based in Eudora, Kansas.
Business Info:
We are a local cut flower farm located in Eudora, Kansas, founded by Corinne Haldwick. What started as a passion for agriculture and search for more joy in daily life has blossomed into a small business dedicated to providing the community with beautiful, fresh, and sustainable flowers. We specialize in local, seasonal blooms, ensuring that every petal reflects the care and dedication we pour into our craft. Our mission is to deliver the highest quality flowers directly to our customers through local farmers markets and to florists who share our commitment to sustainability. Join us in celebrating the beauty of nature, one bloom at a time!
Contact Details:
Corinne Haldwick
Owner
Phone 913-555-0147
Facebook: Rosalind Thorpe Gardens
Instagram: @RosalindThorpeGardens
Website: RosalindThorpeGardens.example
Target Market(s)
Wholesale to Florists and Direct to Consumer via Farmers Market
Industry/Entity Type
Florist, Farm
Contact Information for Business Card
Name, Contact Info, Logo
Look and feel
Each slider illustrates characteristics of the customer's brand and the style your logo design should communicate.

```html
<!DOCTYPE html>
<html lang="en">
<head>
<meta charset="utf-8">
<title>Rosalind Thorpe Gardens – Business Card</title>
<link rel="stylesheet" href="https://fonts.googleapis.com/css2?family=Cormorant+Garamond:wght@500&family=Lato:wght@400&display=swap">
<style>
  :root {
    --teal: #0b2a30;
    --teal-ink: #0f3137;
    --paper: #ffffff;
    --stage-light: #ececec;
    --stage-dark: #7f7f7f;
    --rule: #1b2f33;
  }
  html, body {
    margin: 0;
    padding: 0;
    width: 1200px;
    height: 1000px;
    overflow: hidden;
  }
  .stage {
    position: relative;
    width: 1200px;
    height: 1000px;
    background: radial-gradient(ellipse at 50% 50%, var(--stage-light) 0%, #c4c4c4 55%, var(--stage-dark) 100%);
  }
  .card {
    position: absolute;
    left: 200px;
    width: 801px;
    height: 458px;
    border-radius: 18px;
    box-shadow: 0 2px 8px rgba(0,0,0,0.18);
    overflow: hidden;
  }
  .card--front {
    top: 22px;
    background: var(--teal);
  }
  .card--back {
    top: 498px;
    background: var(--paper);
  }
  .wordmark {
    position: absolute;
    font-family: "Cormorant Garamond", Georgia, serif;
    font-weight: 500;
    text-transform: uppercase;
    text-align: center;
    letter-spacing: 0.14em;
    line-height: 1.15;
  }
  .wordmark--front {
    left: 400px;
    top: 240px;
    width: 280px;
    margin-left: -140px;
    margin-top: -40px;
    color: var(--paper);
    font-size: 30px;
  }
  .wordmark--back {
    left: 565px;
    top: 229px;
    width: 380px;
    margin-left: -190px;
    margin-top: -52px;
    color: var(--teal-ink);
    font-size: 40px;
  }
  .holder {
    position: absolute;
    left: 35px;
    top: 40px;
  }
  .holder__name {
    margin: 0;
    font-family: "Cormorant Garamond", Georgia, serif;
    font-weight: 500;
    font-size: 31px;
    letter-spacing: 0.02em;
    text-transform: uppercase;
    color: var(--teal-ink);
    line-height: 1;
  }
  .holder__role {
    margin: 10px 0 0;
    font-family: "Lato", Arial, sans-serif;
    font-size: 19px;
    color: var(--teal-ink);
  }
  .holder__rule {
    width: 130px;
    height: 2px;
    background: var(--rule);
    margin-top: 18px;
  }
  .contacts {
    position: absolute;
    left: 36px;
    top: 302px;
    margin: 0;
    padding: 0;
    list-style: none;
    font-family: "Lato", Arial, sans-serif;
    font-size: 20px;
    color: #111;
  }
  .contacts li {
    display: flex;
    align-items: center;
    height: 32px;
  }
  .contacts svg {
    width: 17px;
    height: 17px;
    margin-right: 8px;
    flex: none;
  }
</style>
</head>
<body>
<div class="stage">

  <section class="card card--front" aria-label="Card front">
    <div class="wordmark wordmark--front">Rosalind Thorpe<br>Gardens</div>
  </section>

  <section class="card card--back" aria-label="Card back">
    <div class="holder">
      <h1 class="holder__name">Corinne Haldwick</h1>
      <p class="holder__role">Owner</p>
      <div class="holder__rule"></div>
    </div>

    <ul class="contacts">
      <li>
        <svg viewBox="0 0 24 24" aria-hidden="true"><path fill="#111" d="M6.6 10.8a15.1 15.1 0 0 0 6.6 6.6l2.2-2.2a1 1 0 0 1 1-.25 11.4 11.4 0 0 0 3.6.6 1 1 0 0 1 1 1V20a1 1 0 0 1-1 1A17 17 0 0 1 3 4a1 1 0 0 1 1-1h3.5a1 1 0 0 1 1 1c0 1.25.2 2.45.6 3.6a1 1 0 0 1-.25 1z"/></svg>
        913-555-0147
      </li>
      <li>
        <svg viewBox="0 0 24 24" aria-hidden="true"><circle cx="12" cy="12" r="8" fill="#111"/></svg>
        Rosalind Thorpe Gardens
      </li>
      <li>
        <svg viewBox="0 0 24 24" aria-hidden="true"><circle cx="12" cy="12" r="8" fill="none" stroke="#111" stroke-width="2.4"/></svg>
        @RosalindThorpeGardens
      </li>
      <li>
        <svg viewBox="0 0 24 24" aria-hidden="true" fill="none" stroke="#111" stroke-width="2"><circle cx="12" cy="12" r="9"/><ellipse cx="12" cy="12" rx="4" ry="9"/><path d="M3 12h18"/></svg>
        RosalindThorpeGardens.example
      </li>
    </ul>

    <div class="wordmark wordmark--back">Rosalind Thorpe<br>Gardens</div>
  </section>

</div>
</body>
</html>
```